Cover für Hauptkatalog
Kompetenter Kontakt. Super schnell wurden die Änderungswünsche umgesetzt. Vielen Dank und bis zum nächsten Mal.
Zielgruppe
BASTUVO GmbH ist ein führender Großhändler in der Hobby- und Bastelbranche. mit unseren weit über 8.000 Produkten beliefern wir Einzelhändler in ganz Europa. Durch unsere Größe sind wir in der Lage sehr schnell auf individuelle Kundenwünsche zu reagieren.
Aufgabenstellung
Wir werden Mitte Dezember einen neuen Kreativ-Katalog mit über 450 Seiten unseren Kunden zur Verfügung stellen. In diesem Zusammenhang soll der Umschlag (Vorder- und Rückseite) in einem neuen, frischen Design erscheinen. Das aktuelle Layout kann unter www.bastuvo-beispiel.com eingesehen werden. Auf der Rückseite soll unsere Adresse stehen.

```html
<!DOCTYPE html>
<html lang="de">
<head>
<meta charset="utf-8">
<title>Bastuvo – Katalog Rückseite</title>
<link rel="stylesheet" href="https://fonts.googleapis.com/css2?family=Lato:wght@300;400&display=swap">
<style>
  :root {
    --ink: #2a3f8f;
    --grey-text: #c3ccd3;
    --paper: #ffffff;
    --s-green: #d9e0a6;
    --s-pink: #eebcc0;
    --s-blue: #b9ccd6;
    --s-taupe: #d3c4bf;
    --s-peach: #f0d3a6;
    --s-lilac: #cbb8da;
    --s-mint: #a9d5be;
    --s-sky: #a5d6e4;
  }
  * { margin: 0; padding: 0; box-sizing: border-box; }
  html, body { width: 1200px; height: 850px; overflow: hidden; background: var(--paper); }
  .cover {
    position: relative; width: 1200px; height: 850px;
    font-family: "Lato", sans-serif; color: var(--ink); background: var(--paper);
  }
  .brand-name {
    position: absolute; font-family: "Lato", sans-serif; font-weight: 400;
    color: var(--ink); line-height: 1; white-space: nowrap;
  }
  .brand-name--top { left: 51px; top: 48px; font-size: 44px; }
  .brand-name--bottom { right: 36px; top: 738px; font-size: 64px; }

  .headline {
    position: absolute; right: 29px; top: 30px; text-align: right;
    font-weight: 300; line-height: 1;
  }
  .headline .de { font-size: 58px; font-weight: 400; letter-spacing: 0.5px; }
  .headline .fr, .headline .en { font-size: 43px; color: var(--grey-text); margin-top: 12px; }
  .headline .en { margin-top: 10px; }

  .photos { position: absolute; left: 0; top: 0; width: 1200px; height: 490px; }

  .stripes { position: absolute; left: 0; top: 491px; width: 1200px; }
  .stripes span { display: block; height: 5px; margin-bottom: 7px; }

  .info { position: absolute; left: 28px; top: 588px; font-size: 16.5px; font-weight: 300; line-height: 19.5px; }
  .addresses { position: absolute; left: 28px; top: 660px; display: flex; }
  .address { font-size: 18px; font-weight: 300; line-height: 20.3px; font-style: normal; }
  .address:first-child { width: 261px; }
  .address .company { font-weight: 400; }
  .website { position: absolute; left: 27px; top: 788px; font-size: 35px; font-weight: 400; }
</style>
</head>
<body>
<main class="cover">
  <div class="brand-name brand-name--top">Bastuvo</div>

  <header class="headline">
    <div class="de"><span style="color:#a9d5be">F</span><span style="color:#d3c4bf">r</span><span style="color:#d9e0a6">e</span><span style="color:#a5d6e4">u</span><span style="color:#a9d5be">d</span><span style="color:#eebcc0">e</span> <span style="color:#cbb8da">a</span><span style="color:#b9ccd6">n</span> <span style="color:#a9d5be">K</span><span style="color:#d3c4bf">r</span><span style="color:#eebcc0">e</span><span style="color:#f0d3a6">a</span><span style="color:#a5d6e4">t</span><span style="color:#cbb8da">i</span><span style="color:#d9e0a6">v</span><span style="color:#b9ccd6">i</span><span style="color:#eebcc0">t</span><span style="color:#a5d6e4">ä</span><span style="color:#cbb8da">t</span></div>
    <div class="fr">Plaisir de créer</div>
    <div class="en">Creative pleasure</div>
  </header>

  <svg class="photos" viewBox="0 0 1200 490" xmlns="http://www.w3.org/2000/svg">
    <defs>
      <linearGradient id="g-ceramic" x1="0" y1="0" x2="1" y2="1"><stop offset="0" stop-color="#7d8f4f"/><stop offset="0.5" stop-color="#6f9fd8"/><stop offset="1" stop-color="#c9dbe6"/></linearGradient>
      <linearGradient id="g-beads" x1="0" y1="0" x2="1" y2="1"><stop offset="0" stop-color="#e7f2c9"/><stop offset="0.5" stop-color="#b7d86b"/><stop offset="1" stop-color="#d8eaa0"/></linearGradient>
      <linearGradient id="g-table" x1="0" y1="0" x2="1" y2="1"><stop offset="0" stop-color="#bcd9e3"/><stop offset="1" stop-color="#e8eef2"/></linearGradient>
      <linearGradient id="g-pinwheel" x1="0" y1="0" x2="1" y2="1"><stop offset="0" stop-color="#f28a3a"/><stop offset="0.45" stop-color="#e56fb0"/><stop offset="1" stop-color="#6aa6dc"/></linearGradient>
      <linearGradient id="g-flowers" x1="0" y1="0" x2="0" y2="1"><stop offset="0" stop-color="#9dbb6a"/><stop offset="0.5" stop-color="#c77ab0"/><stop offset="1" stop-color="#4f8a3c"/></linearGradient>
      <linearGradient id="g-decor" x1="0" y1="0" x2="1" y2="1"><stop offset="0" stop-color="#f2f0ee"/><stop offset="0.55" stop-color="#5fb3cf"/><stop offset="1" stop-color="#e7d3df"/></linearGradient>
    </defs>
    <circle cx="144" cy="334" r="97" fill="url(#g-ceramic)" stroke="#b8c4cc" stroke-width="4" role="img" aria-label="Foto: blau bemalte Keramikschalen mit grünen Äpfeln im Garten"/>
    <circle cx="337" cy="226" r="97" fill="url(#g-beads)" stroke="#d9e0a6" stroke-width="4" role="img" aria-label="Foto: grüne und gelbe Glasperlenketten auf weißem Band"/>
    <circle cx="496" cy="375" r="83" fill="url(#g-table)" stroke="#a5d6e4" stroke-width="4" role="img" aria-label="Foto: gedeckter Tisch mit Kerze, Gläsern und Muffins"/>
    <circle cx="722" cy="259" r="111" fill="url(#g-pinwheel)" stroke="#eebcc0" stroke-width="4" role="img" aria-label="Foto: bunte gemusterte Windräder vor Lavendel"/>
    <circle cx="907" cy="375" r="97" fill="url(#g-flowers)" stroke="#cbb8da" stroke-width="4" role="img" aria-label="Foto: bunt verzierte Gartenblumen auf Stäben im Grünen"/>
    <circle cx="1089" cy="300" r="83" fill="url(#g-decor)" stroke="#f0d3a6" stroke-width="4" role="img" aria-label="Foto: bemalte Dekofigur neben pinken Windlichtern am Fenster"/>
  </svg>

  <div class="stripes">
    <span style="background:var(--s-green)"></span>
    <span style="background:var(--s-pink)"></span>
    <span style="background:var(--s-blue)"></span>
    <span style="background:var(--s-taupe)"></span>
    <span style="background:var(--s-peach)"></span>
    <span style="background:var(--s-lilac)"></span>
    <span style="background:var(--s-mint)"></span>
    <span style="background:var(--s-sky)"></span>
  </div>

  <section class="info">
    <p>Weitere Informationen und Bezugsquellennachweis</p>
    <p>Pour toute information complementaire et liste de revendeurs</p>
    <p>Further information and documentation can be obtained from</p>
  </section>

  <section class="addresses">
    <address class="address">
      <div class="company">BASTUVO AG</div>
      <div>Seeweg 8</div>
      <div>CH-4410 Musterdorf</div>
      <div>Phone: +41 61 555 01 20</div>
      <div>Fax: +41 61 555 01 21</div>
      <div>info@bastuvo-beispiel.ch</div>
    </address>
    <address class="address">
      <div class="company">BASTUVO GmbH</div>
      <div>Lindenallee 5</div>
      <div>D-79000 Beispielstadt</div>
      <div>Phone: +49 7600 5550 0</div>
      <div>Fax: +49 7600 5551</div>
      <div>info@bastuvo-beispiel.de</div>
    </address>
  </section>

  <div class="website">www.bastuvo-beispiel.com</div>

  <div class="brand-name brand-name--bottom">Bastuvo</div>
</main>
</body>
</html>
```